Newspaper ad for web design services

I have a paid space in a local newspaper size: 4.5085" W x 2.6875" H.
I want to use it for promoting my web design services.
Designers have the freedom to design the ad and the offer.
The goal is to have people contact me for business web design.
I published one ad last month and it totally failed to bring any attention.
Feel free to change or add anything you think can be more effective to attract potential customers (I can create any tripwire you consider will work)
Target: Houston-based business owners looking to get a new website or to update their existing one.

```html
<!DOCTYPE html>
<html lang="en">
<head>
<meta charset="utf-8">
<title>Vela Studio – Newspaper Ad</title>
<link rel="stylesheet" href="https://fonts.googleapis.com/css2?family=Montserrat:wght@500;700&family=Oswald:wght@600&display=swap">
<style>
  :root {
    --brand-blue: #3d63b0;
    --paper: #ffffff;
    --ink: #1d1d1f;
    --badge-yellow: #fff200;
    --badge-ink: #2a3f8f;
    --icon-fill: #6b6f78;
    --screen-dark: #2b2b2e;
    --screen-mid: #6f6a66;
    --cover-dark: #14161f;
    --cover-mid: #2a3150;
  }
  * { margin: 0; padding: 0; box-sizing: border-box; }
  html, body { width: 1200px; height: 715px; overflow: hidden; background: var(--paper); }
  .ad {
    position: relative; width: 1200px; height: 715px; overflow: hidden;
    background: var(--paper); font-family: "Montserrat", Arial, sans-serif; color: var(--paper);
  }
  .ad__backdrop { position: absolute; inset: 0; }
  .brand { position: absolute; left: 60px; top: 58px; display: flex; align-items: center; gap: 14px; }
  .brand__mark { width: 78px; height: 78px; border-radius: 14px; background: var(--brand-blue); }
  .brand__name { color: var(--ink); font-weight: 500; font-size: 42px; line-height: 1.0; }
  .headline { position: absolute; left: 456px; top: 50px; }
  .headline__lead { font-weight: 700; font-size: 30px; line-height: 1; white-space: nowrap; }
  .headline__main { margin-top: 18px; font-weight: 700; font-size: 58px; line-height: 1.07; white-space: nowrap; letter-spacing: 0.5px; }
  .video-mockup {
    position: absolute; left: 37px; top: 255px; width: 537px; height: 425px; border-radius: 14px;
    background: linear-gradient(160deg, var(--screen-dark) 0%, var(--screen-mid) 55%, var(--screen-dark) 100%);
  }
  .benefits { position: absolute; left: 613px; top: 277px; list-style: none; }
  .benefit { display: flex; align-items: center; height: 72px; margin-bottom: 14px; }
  .benefit__icon {
    width: 72px; height: 72px; border-radius: 50%; background: var(--icon-fill);
    border: 2px solid var(--paper); flex: none; display: flex; align-items: center; justify-content: center;
  }
  .benefit__icon svg { width: 40px; height: 40px; fill: none; stroke: var(--paper); stroke-width: 2; stroke-linecap: round; stroke-linejoin: round; }
  .benefit__text { margin-left: 16px; font-weight: 500; font-size: 32px; line-height: 1.02; }
  .ebook-cover {
    position: absolute; left: 1007px; top: 265px; width: 184px; height: 277px;
    background: linear-gradient(170deg, var(--cover-dark) 0%, var(--cover-dark) 60%, var(--cover-mid) 100%);
    box-shadow: 4px 4px 10px rgba(0,0,0,0.35);
  }
  .offer-badge {
    position: absolute; left: 914px; top: 448px; width: 184px; height: 184px; border-radius: 50%;
    background: var(--badge-yellow); color: var(--badge-ink);
    display: flex; align-items: center; justify-content: center; text-align: center;
    font-family: "Oswald", "Arial Narrow", sans-serif; font-weight: 600; font-size: 31px; line-height: 1.12;
  }
  .visit { position: absolute; left: 523px; top: 656px; font-weight: 700; font-size: 34px; white-space: nowrap; }
</style>
</head>
<body>
<main class="ad">
  <svg class="ad__backdrop" width="1200" height="715" viewBox="0 0 1200 715" aria-hidden="true">
    <path fill="var(--brand-blue)" d="M418 0 C402 90 362 168 293 222 C400 238 500 250 572 262 L480 715 L1200 715 L1200 0 Z"/>
  </svg>

  <div class="brand">
    <div class="brand__mark"></div>
    <div class="brand__name">Vela<br>Studio</div>
  </div>

  <header class="headline">
    <p class="headline__lead">The ONE easy change will make your</p>
    <h1 class="headline__main">BUSINESS WEBISTE<br>DOUBLE YOUR SALES</h1>
  </header>

  <div class="video-mockup" role="img" aria-label="Desktop monitor showing a welcome video of Marco, the designer, holding a coffee mug in his studio"></div>

  <ul class="benefits">
    <li class="benefit">
      <span class="benefit__icon"><svg viewBox="0 0 40 40"><circle cx="20" cy="12" r="5"/><path d="M10 28 c0-6 4-9 10-9 s10 3 10 9"/></svg></span>
      <span class="benefit__text">Get more new<br>Customers</span>
    </li>
    <li class="benefit">
      <span class="benefit__icon"><svg viewBox="0 0 40 40"><rect x="7" y="11" width="26" height="19" rx="3"/><path d="M24 18 h9 v6 h-9 z"/></svg></span>
      <span class="benefit__text">Buy More</span>
    </li>
    <li class="benefit">
      <span class="benefit__icon"><svg viewBox="0 0 40 40"><path d="M20 7 l3.5 7.5 8 1 -6 5.5 1.6 8 -7.1-4 -7.1 4 1.6-8 -6-5.5 8-1 z"/></svg></span>
      <span class="benefit__text">Get more<br>Reviews</span>
    </li>
    <li class="benefit">
      <span class="benefit__icon"><svg viewBox="0 0 40 40"><path d="M8 17 h6 l14-7 v20 l-14-7 h-6 z"/><path d="M13 23 l2 8"/></svg></span>
      <span class="benefit__text">Refer more<br>customers</span>
    </li>
  </ul>

  <div class="ebook-cover" role="img" aria-label="E-book cover: The ONE easy change will make your business website double your sales, a step-by-step action guide with a rocket in space"></div>

  <div class="offer-badge">DOWNLOAD<br>THE FREE<br>E-BOOK</div>

  <p class="visit">Visit : velastudio.com/website</p>
</main>
</body>
</html>
```